Business Card Design for a Personal Trainer

I need a business card design for my job as a personal trainer. It should have a unique, modern and exclusive design. On the front there should be only my logo with my name and my job. 0162/3819204 Tobias Lendhart Wiesengrundweg 14 80417 Munich Germany The most important contact information is the web adress. it can be bigger than the rest, but its not necessary. The card should be 8,5cmx5,5cm big. Font: Roboto. Colors: black, white, gray, 56c1ff.

```html
<!DOCTYPE html>
<html lang="de">
<head>
<meta charset="utf-8">
<title>Tobias Lendhart – Personal Trainer Visitenkarte</title>
<link href="https://fonts.googleapis.com/css2?family=Roboto:wght@400;500&display=swap" rel="stylesheet">
<style>
  :root {
    --bg: #e4e4e6;
    --card-white: #ffffff;
    --card-blue: #7ba4d3;
    --band-blue: #6d9bd6;
    --ink: #141414;
    --white: #ffffff;
    --photo-light: #e9e9e9;
    --photo-dark: #3a3a3a;
    --forest-light: #f3e6c2;
    --forest-mid: #c9b88c;
    --forest-dark: #6f6a4f;
  }
  * { margin: 0; padding: 0; box-sizing: border-box; }
  html, body { width: 1200px; height: 864px; overflow: hidden; }
  body {
    background: var(--bg);
    font-family: "Roboto", Arial, sans-serif;
    display: flex;
    align-items: center;
    justify-content: center;
    gap: 30px;
  }
  .card {
    position: relative;
    width: 560px;
    height: 362px;
    overflow: hidden;
    background: var(--card-white);
    box-shadow: 0 6px 18px rgba(0,0,0,0.18);
  }
  /* Front card */
  .card-front .blue-field {
    position: absolute; inset: 0;
    width: 560px; height: 362px;
  }
  .trainer-portrait {
    position: absolute;
    left: 40px; bottom: 0;
    width: 200px; height: 300px;
    background: linear-gradient(180deg, var(--photo-light) 0%, #9a9a9a 35%, var(--photo-dark) 100%);
    border-radius: 90px 90px 0 0;
  }
  .contact-block {
    position: absolute;
    right: 30px; top: 58px;
    text-align: right;
    color: var(--ink);
  }
  .brand-name {
    color: var(--white);
    font-size: 27px;
    font-weight: 500;
    letter-spacing: 1px;
    line-height: 1;
  }
  .brand-role {
    display: flex;
    align-items: center;
    gap: 8px;
    justify-content: flex-end;
    margin-top: 6px;
    color: var(--white);
    font-size: 10px;
    letter-spacing: 3px;
  }
  .brand-role::before, .brand-role::after {
    content: ""; flex: 1; height: 1px; background: var(--white);
  }
  .brand-role::after { flex: 0 0 30px; }
  .person-name {
    margin-top: 26px;
    color: var(--white);
    font-size: 19px;
    font-weight: 500;
    letter-spacing: 0.5px;
  }
  .contact-list {
    list-style: none;
    margin-top: 20px;
    font-size: 14px;
    line-height: 20px;
  }
  .contact-list li {
    display: flex; align-items: center; justify-content: flex-end; gap: 8px;
  }
  .contact-list .icon { width: 12px; height: 12px; flex: none; }
  .contact-list .no-icon { width: 12px; flex: none; }
  /* Back card */
  .scene-photo {
    position: absolute; left: 0; top: 0;
    width: 560px; height: 248px;
    background:
      radial-gradient(ellipse at 35% 20%, var(--forest-light) 0%, transparent 55%),
      linear-gradient(180deg, var(--forest-mid) 0%, var(--forest-dark) 100%);
  }
  .web-band {
    position: absolute; left: 0; bottom: 0;
    width: 560px; height: 114px;
    background: var(--band-blue);
    display: flex; align-items: center; justify-content: center;
  }
  .web-address {
    color: var(--white);
    font-size: 30px;
    letter-spacing: 1.5px;
  }
</style>
</head>
<body>
  <section class="card card-front">
    <svg class="blue-field" viewBox="0 0 560 362" aria-hidden="true">
      <path d="M250 0 Q345 190 175 362 L560 362 L560 0 Z" fill="var(--card-blue)"/>
    </svg>
    <div class="trainer-portrait" role="img" aria-label="Schwarz-Weiß-Porträt des Trainers mit verschränkten Armen"></div>
    <div class="contact-block">
      <div class="brand-name">TOBIAS LENDHART</div>
      <div class="brand-role">PERSONAL TRAINER</div>
      <div class="person-name">Tobias Lendhart</div>
      <ul class="contact-list">
        <li>0162/3819204
          <svg class="icon" viewBox="0 0 12 12"><path d="M3 1l2 2-1 1.5c.6 1.3 1.6 2.3 2.9 2.9L8.4 6.4l2 2L9.5 10.5C5 10 2 7 1.5 2.5Z" fill="var(--white)"/></svg>
        </li>
        <li>t.lendhart@mailbox.de
          <svg class="icon" viewBox="0 0 12 12"><rect x="1" y="2.5" width="10" height="7" fill="var(--white)"/><path d="M1 2.5l5 4 5-4" stroke="var(--card-blue)" fill="none"/></svg>
        </li>
        <li>Wiesengrundweg 14
          <svg class="icon" viewBox="0 0 12 12"><path d="M6 11S2 6.8 2 4.5a4 4 0 0 1 8 0C10 6.8 6 11 6 11Z" fill="var(--white)"/><circle cx="6" cy="4.5" r="1.4" fill="var(--card-blue)"/></svg>
        </li>
        <li>80417 München<span class="no-icon"></span></li>
      </ul>
    </div>
  </section>

  <section class="card card-back">
    <div class="scene-photo" role="img" aria-label="Foto einer Frau beim Dehnen im sonnigen Wald"></div>
    <div class="web-band">
      <span class="web-address">www.tobiaslendhart.de</span>
    </div>
  </section>
</body>
</html>
```